Mortgage Protection Insurance Flyer

The target audience are new home owners so the design needs to be clean and simple.

This a primarily for Final Expense Insurance, but need an area where it says "We Also Specialize In:"
- Medicare Supplement Insurance (MediGap)
- Annuities
- Final Expense

All flyer versions need to be editable. Colors to be used are red, white or black. Refer to my website for colors and photos (corvantshield.com). Will attach my logo and a flyer that I found online that is the format that I am looking for (for 8.5 in. x 11 in version). Need flyer in standard letter size 8.5 in. x11 in. but also in 8.5 in. x 5.5 in and 5.0 in. x 8.0 in. All sizes to be portrait oriented. If picked as winning design, need all flyer versions in full color, also in grey scale and files in all industry file types.

Content can be taken from my website..... corvantshield.com

Do NOT submit if you are not willing to provide all versions as described above for the original project price.

Must use royalty-free stock photos please.

Target Market(s)

New homeowners looking for insurance to protect there mortgage payments

Industry/Entity Type

Life Insurance

Colors
f69fa3

Requirements
Must have
• Colors to be used are red, white or black.
• Need flyer in standard letter size 8.5 in. x11 in. but also in 3.5 in. x 8.5 in (Full Bleed 3.75 in by 8.75 in.) and 4.0 in. x 6.0 in. (Full Bleed 4.12 in x 6.12 in) Each design tailored to the size dimensions (So no squeezing 8.5 x 11 design into a 4.0 x 6.0 space.) All sizes to be portrait oriented. If picked as winning design, need all flyer versions in full color, also in grey scale and files in all file types.
• Do not need physical address on flyer, do need email address on flyer though - tkelwer@corvantshield.com
• So phone number should be prominent, email address and website address should also be contact area.
• If you can not agree to terms above, do not submit any designs.
• Need facebook & twitter logos somewhere in contact info area.
Nice to have
• See sample flyers I have attached.
• White background with red used as primary graphic color and black used as secondary graphic if needed.
• font to be used should similar to one used in logo.

```html
<!DOCTYPE html>
<html lang="en">
<head>
<meta charset="utf-8">
<title>Corvant Shield Insurance – Final Expense Flyer</title>
<link href="https://fonts.googleapis.com/css2?family=Anton&family=Lato:wght@400;700;900&family=Roboto+Condensed:wght@500;700&display=swap" rel="stylesheet">
<style>
  :root{
    --red:#e10a0a;
    --red-deep:#a8141a;
    --ink:#1e1e1e;
    --charcoal:#333333;
    --grey-band:#d3d3d3;
    --hero-grey:#eceef1;
    --white:#ffffff;
  }
  *{box-sizing:border-box;margin:0;padding:0}
  html,body{width:1200px;height:1200px;overflow:hidden;background:#ffffff}
  .flyer{
    position:absolute;left:164px;top:24px;width:908px;height:1175px;
    transform:scale(0.96);transform-origin:0 0;
    background:var(--white);overflow:hidden;
    font-family:'Lato',sans-serif;color:var(--ink);
  }
  .decor{position:absolute;inset:0;width:908px;height:1175px}
  .abs{position:absolute}
  .brand{left:36px;top:72px;display:flex;align-items:center;gap:10px;
    font-family:'Lato',sans-serif;font-weight:900;font-size:30px;letter-spacing:1px;color:var(--ink)}
  .brand-mark{width:16px;height:16px;background:var(--red)}
  .headline{left:63px;top:234px;font-family:'Anton',sans-serif;line-height:1;text-transform:uppercase}
  .headline .l1{font-size:68px;color:var(--ink);display:block}
  .headline .l2{font-size:68px;color:var(--red);display:block;margin-top:8px}
  .headline .l3{font-size:42px;color:var(--ink);display:block;margin-top:8px}
  .section-title{font-family:'Lato',sans-serif;font-weight:900;font-size:19px;color:var(--red)}
  .body-copy{font-size:14.3px;line-height:18px;color:var(--charcoal);width:440px}
  .rates{left:35px;top:672px;width:430px}
  .rate-row{display:flex;gap:5px;height:22px;margin-bottom:12px;font-family:'Roboto Condensed',sans-serif;font-weight:500;font-size:14px}
  .rate-label{width:290px;background:var(--grey-band);padding:2px 8px;color:var(--ink)}
  .rate-value{width:135px;background:var(--red);color:var(--white);text-align:center;padding:2px 0;font-weight:700}
  .benefits{left:530px;top:388px;width:356px;height:428px;border-radius:26px;
    background:linear-gradient(180deg,#ff0000 0%,#e20d0d 55%,#b8151a 100%)}
  .benefits-tab{left:513px;top:426px;height:32px;width:157px;background:var(--charcoal);
    border-radius:0 18px 18px 0;color:var(--white);font-weight:900;font-size:25px;padding:0 0 0 28px;line-height:32px}
  .benefit-list{left:558px;top:480px;width:320px;list-style:none}
  .benefit-list li{display:flex;gap:10px;color:var(--white);font-weight:700;font-size:14.3px;line-height:18px;margin-bottom:18px}
  .benefit-list svg{flex:none;width:18px;height:18px}
  .specialties{left:543px;top:874px;list-style:none}
  .specialties li{display:flex;gap:8px;align-items:center;font-size:16px;color:var(--ink);margin-bottom:8px}
  .specialties svg{width:18px;height:18px;flex:none}
  .footnote{left:542px;top:983px;font-size:10.5px;line-height:14px;color:var(--charcoal);width:330px}
  .call{left:37px;top:1060px;color:var(--white);font-weight:700}
  .call .label{font-size:30px;display:block}
  .call .phone{font-size:46px;font-weight:900;display:block;margin-top:-2px}
  .contact{top:1103px;display:flex;align-items:center;gap:10px;color:var(--white);font-weight:700;font-size:13px}
  .contact .ring{width:35px;height:35px;border:1.5px solid var(--white);border-radius:50%;display:flex;align-items:center;justify-content:center}
</style>
</head>
<body>
<div class="flyer">
  <svg class="decor" viewBox="0 0 908 1175" aria-hidden="true">
    <defs>
      <linearGradient id="heroGrey" x1="0" y1="0" x2="1" y2="1">
        <stop offset="0" stop-color="#e4e6ea"/><stop offset="1" stop-color="#f3f4f6"/>
      </linearGradient>
      <linearGradient id="photoTone" x1="0" y1="0" x2="1" y2="1">
        <stop offset="0" stop-color="#dfe3e8"/><stop offset="0.5" stop-color="#e9ddd2"/><stop offset="1" stop-color="#f1ece6"/>
      </linearGradient>
      <linearGradient id="footRed" x1="0" y1="0" x2="0" y2="1">
        <stop offset="0" stop-color="#e10a0a"/><stop offset="1" stop-color="#9e151a"/>
      </linearGradient>
    </defs>
    <rect x="0" y="0" width="908" height="480" fill="url(#heroGrey)"/>
    <rect role="img" aria-label="Photo of a smiling senior couple embracing" x="360" y="0" width="548" height="400" fill="url(#photoTone)"/>
    <path d="M0 190 C170 190 360 110 490 0 L0 0 Z" fill="#ffffff"/>
    <path d="M0 186 C170 186 360 106 487 0" fill="none" stroke="#2b2b2b" stroke-width="7"/>
    <path d="M0 196 C175 196 370 112 500 0" fill="none" stroke="#e10a0a" stroke-width="3"/>
    <path d="M0 430 C170 470 420 460 560 440 C700 418 820 385 908 385 L908 1175 L0 1175 Z" fill="#ffffff"/>
    <path d="M0 432 C170 472 420 462 560 442 C700 420 820 387 908 387" fill="none" stroke="#2b2b2b" stroke-width="14"/>
    <path d="M0 460 C170 500 420 488 560 466 C700 444 820 408 908 402" fill="none" stroke="#e10a0a" stroke-width="4"/>
    <path d="M0 1050 C80 1030 160 1025 300 1045 C440 1065 600 1080 720 1060 C800 1045 860 1010 908 985 L908 1175 L0 1175 Z" fill="url(#footRed)"/>
    <path d="M0 1050 C80 1030 160 1025 300 1045 C440 1065 600 1080 720 1060 C800 1045 860 1010 908 985" fill="none" stroke="#2b2b2b" stroke-width="6"/>
    <path d="M0 1062 C90 1042 170 1040 300 1058 C440 1077 600 1090 720 1072 C800 1058 862 1024 908 1002" fill="none" stroke="#ffffff" stroke-width="4"/>
  </svg>

  <div class="abs brand"><span class="brand-mark"></span>CORVANT SHIELD</div>

  <h1 class="abs headline"><span class="l1">Our</span><span class="l2">Plans are</span><span class="l3">Based on yours</span></h1>

  <h2 class="abs section-title" style="left:35px;top:537px">Final Expense Insurance</h2>
  <p class="abs body-copy" style="left:35px;top:574px">Final Expense Insurance is a type of permanent life insurance where the death benefit is used to cover (but not limited to) medical costs, funeral costs and other end-of-life expenses. It is a budget friendly option with a death benefit of up to $40k.</p>

  <div class="abs rates">
    <div class="rate-row"><span class="rate-label">Monthly premiums as low as</span><span class="rate-value">$11*</span></div>
    <div class="rate-row"><span class="rate-label">Death Benefits as high as</span><span class="rate-value">$40,000</span></div>
  </div>

  <p class="abs body-copy" style="left:35px;top:760px">Unforeseen events and a lack of the right kind of insurance can spell trouble quickly. Contact us today, to set up a free assessment time. We will analyze your insurance needs and get you and your family the right coverage quickly at a budget friendly price.</p>
  <p class="abs body-copy" style="left:35px;top:851px">We have been helping clients in Northern Idaho/Eastern Washington prepare for the unknown.</p>
  <p class="abs body-copy" style="left:35px;top:904px">We have access to the industry's top insurance carriers so you can get the right coverage, that fits your budget.</p>
  <p class="abs body-copy" style="left:35px;top:963px">Find out how we can give you the peace of mind knowing your family wont have a financial burden if something were to happen to you.</p>

  <div class="abs benefits"></div>
  <div class="abs benefits-tab">Benefits:</div>
  <ul class="abs benefit-list">
    <li><svg viewBox="0 0 18 18"><circle cx="9" cy="9" r="7.5" fill="none" stroke="#fff" stroke-width="1.5"/><path d="M5.5 9.2l2.3 2.3 4.5-4.6" fill="none" stroke="#fff" stroke-width="1.6"/></svg>All plans we offer are state regulated</li>
    <li><svg viewBox="0 0 18 18"><circle cx="9" cy="9" r="7.5" fill="none" stroke="#fff" stroke-width="1.5"/><path d="M5.5 9.2l2.3 2.3 4.5-4.6" fill="none" stroke="#fff" stroke-width="1.6"/></svg>Relatively low monthly premiums</li>
    <li><svg viewBox="0 0 18 18"><circle cx="9" cy="9" r="7.5" fill="none" stroke="#fff" stroke-width="1.5"/><path d="M5.5 9.2l2.3 2.3 4.5-4.6" fill="none" stroke="#fff" stroke-width="1.6"/></svg>Premiums can never increase</li>
    <li><svg viewBox="0 0 18 18"><circle cx="9" cy="9" r="7.5" fill="none" stroke="#fff" stroke-width="1.5"/><path d="M5.5 9.2l2.3 2.3 4.5-4.6" fill="none" stroke="#fff" stroke-width="1.6"/></svg>Your policy can never be cancelled as long as you pay your premium</li>
    <li><svg viewBox="0 0 18 18"><circle cx="9" cy="9" r="7.5" fill="none" stroke="#fff" stroke-width="1.5"/><path d="M5.5 9.2l2.3 2.3 4.5-4.6" fill="none" stroke="#fff" stroke-width="1.6"/></svg>No medical exams</li>
    <li><svg viewBox="0 0 18 18"><circle cx="9" cy="9" r="7.5" fill="none" stroke="#fff" stroke-width="1.5"/><path d="M5.5 9.2l2.3 2.3 4.5-4.6" fill="none" stroke="#fff" stroke-width="1.6"/></svg>Guaranteed Death Benefit</li>
    <li><svg viewBox="0 0 18 18"><circle cx="9" cy="9" r="7.5" fill="none" stroke="#fff" stroke-width="1.5"/><path d="M5.5 9.2l2.3 2.3 4.5-4.6" fill="none" stroke="#fff" stroke-width="1.6"/></svg>Many policies we offer are Guaranteed Acceptance, "Day 1" coverage, have a child/grandchild rider and/or have an accelerated death benefit rider</li>
  </ul>

  <h2 class="abs section-title" style="left:543px;top:843px">We Also Specialize In:</h2>
  <ul class="abs specialties">
    <li><svg viewBox="0 0 18 18"><circle cx="9" cy="9" r="7.5" fill="none" stroke="#e10a0a" stroke-width="1.5"/><path d="M5.5 9.2l2.3 2.3 4.5-4.6" fill="none" stroke="#e10a0a" stroke-width="1.6"/></svg>Medicare Supplement Insurance (Medigap)</li>
    <li><svg viewBox="0 0 18 18"><circle cx="9" cy="9" r="7.5" fill="none" stroke="#e10a0a" stroke-width="1.5"/><path d="M5.5 9.2l2.3 2.3 4.5-4.6" fill="none" stroke="#e10a0a" stroke-width="1.6"/></svg>Annuities</li>
    <li><svg viewBox="0 0 18 18"><circle cx="9" cy="9" r="7.5" fill="none" stroke="#e10a0a" stroke-width="1.5"/><path d="M5.5 9.2l2.3 2.3 4.5-4.6" fill="none" stroke="#e10a0a" stroke-width="1.6"/></svg>Mortgage Protection Insurance</li>
  </ul>
  <p class="abs footnote">*Based on an insured that is a 65 year old, non-smoking female that has no medical conditions with a death benefit of $2k</p>

  <div class="abs call"><span class="label">Call us now:</span><span class="phone">(208)555.0147</span></div>
  <div class="abs contact" style="left:400px">
    <span class="ring"><svg width="16" height="12" viewBox="0 0 16 12"><rect x="0.75" y="0.75" width="14.5" height="10.5" fill="none" stroke="#fff" stroke-width="1.5"/><path d="M1 1l7 6 7-6" fill="none" stroke="#fff" stroke-width="1.5"/></svg></span>
    tkelwer@corvantshield.com
  </div>
  <div class="abs contact" style="left:682px">
    <span class="ring"><svg width="18" height="18" viewBox="0 0 18 18"><circle cx="9" cy="9" r="7.5" fill="none" stroke="#fff" stroke-width="1.4"/><ellipse cx="9" cy="9" rx="3.3" ry="7.5" fill="none" stroke="#fff" stroke-width="1.2"/><path d="M1.5 9h15M2.8 5h12.4M2.8 13h12.4" stroke="#fff" stroke-width="1.1"/></svg></span>
    corvantshield.com
  </div>
</div>
</body>
</html>
```